We need a flyer design to promote Tavendale & Quill Landscaping and Lawn Maintenance.

The flyer needs to be have:-
1) A great head line ( When quality matters)
2) A really awesome offer ( no obligation free trial mow)
3) A sense of scarcity (Due to time restraints, we can only take limited number of free lawn jobs. This offer is only available to the first 20 callers)
4) A call to action (Call now to avoid disappointment)
5) Contact details (Tavendale & Quill Landscaping and Lawn Maintenance 0452 768 205)

The layout of the entire flyer should come across to potential customers as

1) simple to understand what Tavendale & Quill offer (not overcrowd with messages; the main aim is to communicate across our services.)

The list of services that Tavendale & Quill provide will be:-

- Lawn Mowing - Pruning - Weeding
- Mulching - Edging - Hedging
- Trimming - Fertilising - Garden maintenance
- Weekly, fortnightly or monthly programs

Thank you.

```html
<!DOCTYPE html>
<html lang="en">
<head>
<meta charset="utf-8">
<title>Tavendale &amp; Quill Landscaping – Flyer</title>
<link href="https://fonts.googleapis.com/css2?family=Caladea:wght@700&family=Alegreya:wght@700&family=Arimo:wght@700&display=swap" rel="stylesheet">
<style>
  :root {
    --backdrop: #ece6dc;
    --paper: #ffffff;
    --brown: #3d2a20;
    --maroon: #5a2419;
    --green-deep: #4a7320;
    --green-mid: #8cc152;
    --green-soft: #c9e3a4;
    --green-pale: #eaf5dc;
  }
  * { margin: 0; padding: 0; box-sizing: border-box; }
  html, body { width: 1200px; height: 913px; overflow: hidden; }
  body { background: var(--backdrop); position: relative; }

  .flyer {
    position: absolute;
    left: 301px; top: 94px;
    width: 600px; height: 771px;
    transform: scale(0.977);
    transform-origin: top left;
    background: var(--paper);
    box-shadow: 0 4px 14px rgba(0,0,0,0.22);
    overflow: hidden;
  }

  .header-wash {
    position: absolute; left: 0; top: 0; width: 110px; height: 190px;
    background: linear-gradient(90deg, var(--green-soft), rgba(255,255,255,0));
  }
  .brand {
    position: absolute; left: 0; right: 0; top: 20px; text-align: center;
    font-family: "Caladea", serif; font-weight: 700; color: var(--brown);
  }
  .brand-name { font-size: 38px; line-height: 46px; }
  .brand-sub { font-size: 21px; line-height: 28px; margin-top: 14px; }

  .headline {
    position: absolute; left: 0; right: 0; top: 128px; text-align: center;
    font-family: "Alegreya", serif; font-weight: 700; font-size: 60px;
    color: var(--green-deep); line-height: 70px; letter-spacing: -1.5px;
    transform: scaleX(0.81);
  }

  .band { position: absolute; left: 0; width: 600px; height: 24px; }
  .band-top { top: 190px; background: linear-gradient(90deg, #c2df9c, var(--green-mid) 60%, #9ccd62); }
  .band-bottom { top: 510px; background: linear-gradient(90deg, #ffffff 10%, var(--green-soft) 55%, var(--green-mid)); }

  .photo { position: absolute; top: 214px; height: 296px; }
  .photo-home {
    left: 0; width: 400px;
    background: linear-gradient(180deg, #b9b2a4 0%, #8a7d6c 45%, #5f8a3a 72%, #4f7d2c 100%);
  }
  .photo-play {
    left: 400px; width: 200px;
    background: linear-gradient(180deg, #6f9a47 0%, #86b45c 40%, #9ccc6e 75%, #7fb04e 100%);
  }

  .lower-wash {
    position: absolute; left: 300px; top: 534px; width: 300px; height: 237px;
    background: linear-gradient(90deg, rgba(255,255,255,0), var(--green-pale) 70%, var(--green-soft));
  }

  .offer {
    position: absolute; left: 0; right: 0; top: 543px; text-align: center;
    font-family: "Caladea", serif; font-weight: 700; font-size: 41px;
    color: var(--maroon); line-height: 46px; white-space: nowrap;
  }
  .call {
    position: absolute; left: 0; right: 0; top: 594px; text-align: center;
    font-family: "Caladea", serif; font-weight: 700; font-size: 40px;
    color: var(--green-deep); line-height: 44px; white-space: nowrap;
  }

  .services { position: absolute; left: 0; right: 0; top: 645px; list-style: none; text-align: center; }
  .service {
    position: relative; display: block; width: max-content; margin: 0 auto;
    font-family: "Arimo", sans-serif; font-weight: 700; font-size: 17.5px;
    color: var(--maroon); line-height: 21px; padding: 0 6px;
  }
  .service::before, .service::after {
    content: ""; position: absolute; top: 6px; width: 34px; height: 9px;
  }
  .service::before { right: 100%; background: linear-gradient(90deg, rgba(255,255,255,0), var(--green-soft)); }
  .service::after { left: 100%; background: linear-gradient(90deg, var(--green-soft), rgba(255,255,255,0)); }

  .fine-print {
    position: absolute; left: 0; right: 0; top: 738px; text-align: center;
    font-family: "Arimo", sans-serif; font-weight: 700; font-size: 7.5px;
    color: var(--maroon); line-height: 9px;
  }
</style>
</head>
<body>
  <main class="flyer">
    <div class="header-wash"></div>
    <header class="brand">
      <div class="brand-name">Tavendale &amp; Quill</div>
      <div class="brand-sub">Landscaping and Lawn Maintenance</div>
    </header>
    <h1 class="headline">When Quality Matters</h1>

    <div class="band band-top"></div>
    <div class="photo photo-home" role="img" aria-label="Photo of a large stone-faced family home with a manicured green lawn, trimmed shrubs and a curved concrete path"></div>
    <div class="photo photo-play" role="img" aria-label="Photo of a child hanging from a tree branch in a sunny, leafy park lawn"></div>
    <div class="band band-bottom"></div>

    <div class="lower-wash"></div>
    <h2 class="offer">No Obligation Free trial mow</h2>
    <p class="call">CALL :0452 768 205 NOW!</p>

    <ul class="services">
      <li class="service">Mulching-Edging-Hedging</li>
      <li class="service">Lawn Mowing-Pruning-Weeding</li>
      <li class="service">Trimming-Fertilising-Garden maintenence</li>
      <li class="service">Weekly, fortnightly or monthly programs</li>
    </ul>

    <p class="fine-print">Due to time restraints, we can only take limited<br>number of free lawn jobs. This offer is only<br>available for the first 20 callers</p>
  </main>
</body>
</html>
```